I need a business card design for a new business based in South West Australia.
I specialize in residential window cleaning & general handyman maintenance.

Dale Marsh - 412 SILVER HAWK DETAILING
- Window Cleaning
- House Maintenance

```html
<!DOCTYPE html>
<html lang="en">
<head>
<meta charset="utf-8">
<title>Silver Hawk Detailing – Business Card</title>
<link rel="stylesheet" href="https://fonts.googleapis.com/css2?family=Open+Sans:wght@400;600;800&display=swap">
<style>
  :root {
    --blue: #1a5fb8;
    --blue-deep: #0d4a94;
    --blue-text: #1b4f9c;
    --orange: #f26b1d;
    --ink: #333a44;
    --card: #ffffff;
    --backdrop: #e9ebee;
  }
  * { box-sizing: border-box; margin: 0; padding: 0; }
  html, body { width: 1200px; height: 900px; overflow: hidden; }
  body {
    position: relative;
    background: var(--backdrop);
    font-family: "Open Sans", Arial, sans-serif;
  }
  .card {
    position: absolute;
    background: var(--card);
    border-radius: 16px;
    overflow: hidden;
    box-shadow: 0 8px 24px rgba(0,0,0,.18);
  }
  /* Front */
  .card--front { left: 78px; top: 35px; width: 588px; height: 362px; }
  .front-band {
    position: absolute; left: 0; top: 27px; width: 100%; height: 104px;
    background: linear-gradient(180deg, var(--blue) 0%, var(--blue-deep) 100%);
  }
  .brand-mark {
    position: absolute; left: 86px; top: 31px;
    width: 64px; height: 64px; border-radius: 50%; background: var(--card);
  }
  .front-brand {
    position: absolute; left: 236px; top: 55px;
    color: #fff; font-weight: 800; font-size: 27px; letter-spacing: -.3px; line-height: 1;
  }
  .front-tagline {
    position: absolute; left: 238px; top: 89px;
    color: #fff; font-weight: 800; font-size: 11.5px; letter-spacing: .2px;
  }
  .contact {
    position: absolute; left: 0; top: 165px; width: 100%;
    text-align: center; color: var(--ink);
  }
  .contact__name { color: var(--blue-text); font-weight: 600; font-size: 23px; line-height: 30px; }
  .contact__role { font-size: 15px; line-height: 22px; }
  .contact__line { font-size: 15px; line-height: 24px; display: flex; justify-content: center; align-items: center; gap: 4px; }
  .contact__phone { margin-top: 23px; }
  .contact__address { margin-top: 17px; font-size: 15px; }
  .icon { width: 12px; height: 12px; fill: var(--blue-text); }
  /* Back */
  .card--back { left: 390px; top: 506px; width: 564px; height: 350px; }
  .back-stripe {
    position: absolute; left: 38px; top: 0; width: 44px; height: 100%;
    background: linear-gradient(90deg, var(--blue) 0%, var(--blue-deep) 100%);
  }
  .back-lockup {
    position: absolute; left: 130px; top: 108px; width: 300px;
    display: flex; flex-direction: column; align-items: center;
  }
  .back-lockup .brand-mark--back {
    width: 72px; height: 72px; border-radius: 50%; background: var(--blue);
  }
  .back-brand {
    margin-top: 18px; color: var(--blue); font-weight: 800; font-size: 27px;
    letter-spacing: -.3px; white-space: nowrap; line-height: 1;
  }
  .back-tagline {
    margin-top: 8px; color: var(--orange); font-weight: 800; font-size: 11.5px;
    letter-spacing: .2px; white-space: nowrap;
  }
</style>
</head>
<body>
  <section class="card card--front">
    <div class="front-band"></div>
    <div class="brand-mark"></div>
    <div class="front-brand">SILVER HAWK DETAILING</div>
    <div class="front-tagline">WINDOW CLEANING &amp; HOUSE MAINTENANCE</div>
    <div class="contact">
      <p class="contact__name">Dale Marsh</p>
      <p class="contact__role">Managing Direcator</p>
      <p class="contact__line contact__phone">
        <svg class="icon" viewBox="0 0 24 24" aria-hidden="true"><path d="M3 8c0-3 4-5 9-5s9 2 9 5v2h-5V8c-1-1-7-1-8 0v2H3zM6 11h12l3 9H3z"/></svg>
        823-555-0142
      </p>
      <p class="contact__line">
        <svg class="icon" viewBox="0 0 24 24" aria-hidden="true"><path d="M2 5h20v14H2zM3 6l9 7 9-7v2l-9 7-9-7z" fill-rule="evenodd"/></svg>
        hello@silverhawkmail.com
      </p>
      <p class="contact__address">1234, Address Goes Here Country Name, 123456</p>
    </div>
  </section>

  <section class="card card--back">
    <div class="back-stripe"></div>
    <div class="back-lockup">
      <div class="brand-mark--back"></div>
      <div class="back-brand">SILVER HAWK DETAILING</div>
      <div class="back-tagline">WINDOW CLEANING &amp; HOUSE MAINTENANCE</div>
    </div>
  </section>
</body>
</html>
```